Diverse, up-scale salon needs eye-catching, unique business cards.

We are looking for a unique business card design for our stylist but that can also be multi functional and used for appointment reminder and referrals. I will need a design in a format that I can modify names and titles going forward. In the past we have had a dark background with the logo on one side, and stylist and contact information on the other but we are open to all ideas. I have included our mission statement as well as branded colors below. The statement doesn't need to go on the card, it's just a reference for target market. We need space for the stylists name, title, instagram handle and then the salons phone number, website and address. I am also open to adding a spot for a qr code linked to the stylist instagram or the salon booking link.

primary brand colors:
#333333 #233415 #36502a #93874a #000000
Mission statement:
Vessolin Hair Studio, a high-end salon located in the lively Downtown Farmington, Michigan, is committed to providing exceptional services in a welcoming and relaxed environment to meet the needs of our diverse clientele.
Our salon specializes in contemporary custom haircuts, coloring, extensions, and barbering and beard grooming services. Our team of skilled stylists is passionate and inventive in their hair styling techniques. At the heart of our salon are values centered on quality, innovation, creativity, and above all, comfort. These core values are evident in every appointment across our customizable array of services.
Our goal is to establish a benchmark for exceptional hair care for every human.
Website: www.vessolinhairstudio.example
instagram: @vessolinhairstudio
address: 41782 Pelham Crest Rd, Farmington MI
phone: 248-613-4087

Industry/Entity Type

Hair Salon

Contact Information for Business Card

Stylist name, title, phone, instagram, website, address, (optional qr code)

Requirements
Should not have
• Does not need mission statement on the card.

```html
<!DOCTYPE html>
<html lang="en">
<head>
<meta charset="utf-8">
<title>Vessolin Hair Studio – Business Card</title>
<link href="https://fonts.googleapis.com/css2?family=Lato:wght@400;700;900&display=swap" rel="stylesheet">
<style>
  :root {
    --stage: #2e3033;
    --card: #1b1c1d;
    --gold: #93874a;
    --white: #f2f2f2;
    --muted: #d9d9d9;
  }
  * { margin: 0; padding: 0; box-sizing: border-box; }
  html, body { width: 1200px; height: 952px; overflow: hidden; }
  body {
    background: var(--stage);
    font-family: "Lato", sans-serif;
    display: flex;
    flex-direction: column;
    align-items: center;
    justify-content: center;
    gap: 70px;
  }
  .card {
    position: relative;
    width: 600px;
    height: 343px;
    background: var(--card);
    border-radius: 26px;
    overflow: hidden;
    box-shadow: 0 18px 40px rgba(0,0,0,0.45);
  }
  .edge-band { position: absolute; left: 22px; bottom: 10px; width: 556px; height: 12px; }

  .brand {
    display: flex;
    flex-direction: column;
    align-items: center;
    gap: 14px;
  }
  .brand__ring {
    width: 96px; height: 96px;
    border: 3px solid var(--gold);
    border-radius: 50%;
  }
  .brand__name {
    color: var(--gold);
    font-weight: 900;
    font-size: 20px;
    letter-spacing: 3px;
    text-transform: uppercase;
    text-align: center;
    line-height: 1.25;
  }

  .card--front .brand {
    position: absolute;
    left: 50%; top: 46%;
    transform: translate(-50%, -50%);
  }

  .card--back .brand {
    position: absolute;
    left: 64px; top: 62px;
    width: 190px;
  }
  .card--back .brand__name { font-size: 17px; letter-spacing: 2.5px; }
  .details {
    position: absolute;
    left: 290px; top: 58px;
    width: 290px;
  }
  .stylist__name {
    color: var(--gold);
    font-size: 22px;
    font-weight: 400;
    letter-spacing: 1.5px;
    text-transform: uppercase;
  }
  .stylist__name strong { font-weight: 900; }
  .stylist__title { color: var(--white); font-size: 15px; margin-top: 2px; }
  .stylist__rule { width: 44px; height: 2px; background: var(--white); margin: 10px 0 16px; }
  .contact { list-style: none; display: flex; flex-direction: column; gap: 9px; }
  .contact li {
    display: flex; align-items: flex-start; gap: 10px;
    color: var(--muted); font-size: 13.5px; line-height: 1.3;
  }
  .contact__icon {
    flex: 0 0 18px; width: 18px; height: 18px;
    background: var(--gold); border-radius: 3px;
    display: flex; align-items: center; justify-content: center;
  }
  .contact__icon svg { width: 12px; height: 12px; }
</style>
</head>
<body>

  <section class="card card--front" aria-label="Card front">
    <div class="brand">
      <div class="brand__ring"></div>
      <div class="brand__name">Vessolin<br>Hair Studio</div>
    </div>
    <svg class="edge-band" viewBox="0 0 556 12" preserveAspectRatio="none">
      <rect x="0" y="2" width="268" height="8" fill="var(--gold)"/>
      <rect x="276" y="6" width="280" height="3" fill="var(--white)"/>
    </svg>
  </section>

  <section class="card card--back" aria-label="Card back">
    <div class="brand">
      <div class="brand__ring"></div>
      <div class="brand__name">Vessolin<br>Hair Studio</div>
    </div>

    <div class="details">
      <h1 class="stylist__name">Dorian M. <strong>Kestrel</strong></h1>
      <p class="stylist__title">Managing Director</p>
      <div class="stylist__rule"></div>
      <ul class="contact">
        <li>
          <span class="contact__icon"><svg viewBox="0 0 12 12"><path d="M6 1a3.5 3.5 0 0 0-3.5 3.5C2.5 7 6 11 6 11s3.5-4 3.5-6.5A3.5 3.5 0 0 0 6 1zm0 4.8a1.3 1.3 0 1 1 0-2.6 1.3 1.3 0 0 1 0 2.6z" fill="var(--card)"/></svg></span>
          <span>41782 Pelham Crest Rd<br>Farmington MI</span>
        </li>
        <li>
          <span class="contact__icon"><svg viewBox="0 0 12 12"><path d="M3 1.5l1.6 2.2-.9 1.2a6 6 0 0 0 3.4 3.4l1.2-.9 2.2 1.6-.8 1.6C5.5 10.6 1.4 6.5 1.4 2.3z" fill="var(--card)"/></svg></span>
          <span>248-613-4087</span>
        </li>
        <li>
          <span class="contact__icon"><svg viewBox="0 0 12 12"><circle cx="6" cy="6" r="3.6" fill="none" stroke="var(--card)" stroke-width="1.4"/></svg></span>
          <span>@vessolinhairstudio</span>
        </li>
        <li>
          <span class="contact__icon"><svg viewBox="0 0 12 12"><path d="M2 2l8 3.5-3.3 1.2L5.5 10z" fill="var(--card)"/></svg></span>
          <span>www.vessolinhairstudio.example</span>
        </li>
      </ul>
    </div>

    <svg class="edge-band" viewBox="0 0 556 12" preserveAspectRatio="none">
      <rect x="0" y="6" width="268" height="3" fill="var(--white)"/>
      <rect x="276" y="2" width="280" height="8" fill="var(--gold)"/>
    </svg>
  </section>

</body>
</html>
```